UX - Need some screens design for a Skill Assessment Application

I am building an app to carry out skill assessments. Depending on how the assessment is configured, it may have one or more parts
1. Question based assessment (Multiple Choice, True False, Fill in the blanks"
2. Endorsement by two colleagues - A screen that allows user to pick colleagues based on search and shows the status of pending requests
3. A written submission - a page that explains the format of the submission and a file upload
As each assessment can be configured with or without any of the steps, the assessment UI must be such that these areas get hidden/displayed based on configuration.
Colour codes to be used can be #0e78bb and #ffffff
There will also be a start screen (instructions) and an end screen (results)
Target Market(s)
Enterprise software
Number of Pages Required
4 page

```html
<!DOCTYPE html>
<html lang="en">
<head>
<meta charset="utf-8">
<title>UI/UX Designer Assessment – Endorsement</title>
<link href="https://fonts.googleapis.com/css2?family=Inter:wght@400;500;600;700&display=swap" rel="stylesheet">
<style>
:root{
  --brand:#0e78bb;
  --brand-dark:#0b5aa8;
  --teal:#13939b;
  --ink:#1e1e1e;
  --muted:#555b63;
  --line:#d9dde2;
  --band:#e8eff6;
  --soft:#f3f5f7;
  --white:#ffffff;
}
*{box-sizing:border-box;margin:0;padding:0}
html,body{width:1200px;height:771px;overflow:hidden;background:var(--white);font-family:'Inter',sans-serif;color:var(--ink)}
.abs{position:absolute}
.topbar{position:absolute;left:0;top:0;width:1200px;height:44px;background:var(--brand-dark)}
.brand{left:70px;top:0;height:44px;display:flex;align-items:center;gap:8px;color:var(--white);font-size:15px;font-weight:600}
.brand-dot{width:18px;height:18px;border-radius:50%;background:#5ec3ec}
.nav a{position:absolute;top:0;height:44px;line-height:46px;color:#cfe2f5;font-size:13px;text-decoration:none}
.nav a.active{color:var(--white);font-weight:600;border-bottom:3px solid #46b4e8;height:43px}
.avatar-top{left:1101px;top:8px;width:28px;height:28px;border-radius:50%;background:linear-gradient(135deg,#3a4a66,#c9a896);border:2px solid #fff}
.crumbs{left:57px;top:65px;display:flex;align-items:center;gap:7px;font-size:12px;color:var(--muted)}
.crumbs .link{color:var(--brand);margin-left:6px}
.title{left:88px;top:98px;display:flex;align-items:center;gap:12px;font-size:22px;font-weight:600}
.score{right:88px;top:96px;font-size:28px;font-weight:700}
.score small{font-size:14px;font-weight:600}
.progress{left:0;top:141px;width:1200px;height:7px;background:#f0f2f4}
.progress i{display:block;width:915px;height:100%;background:var(--teal)}
.infoband{left:0;top:148px;width:1200px;height:44px;background:var(--band);border-bottom:1px solid var(--line);font-size:11px}
.infoband .item{position:absolute;top:17px}
.infoband .v{color:var(--brand)}
.infoband .sep{position:absolute;top:14px;width:1px;height:16px;background:#c7cfd8}
.steps .dot{position:absolute;left:82px;width:13px;height:13px;border-radius:50%}
.steps .label{position:absolute;left:110px;font-size:14px}
.section-h{left:366px;top:219px;font-size:15px;font-weight:600}
.save{right:88px;top:221px;display:flex;align-items:center;gap:8px;font-size:11px;color:var(--brand);font-weight:500}
.rule{left:366px;top:254px;width:746px;height:1px;background:var(--line)}
.field{position:absolute;top:273px;height:30px;border:1px solid var(--line);border-radius:3px;font-size:11.5px;display:flex;align-items:center;padding:0 13px;justify-content:space-between}
.row{position:absolute;left:366px;width:468px;height:40px;border:1px solid var(--line);border-radius:3px;display:flex;align-items:center;font-size:12.5px}
.row .cb{width:13px;height:13px;border:1px solid #cfd4da;border-radius:2px;margin:0 8px 0 7px}
.row .pic{width:27px;height:27px;border-radius:50%;margin-right:10px}
.row .name{flex:1;font-weight:500}
.row .role{font-size:11px;color:var(--muted);margin-right:46px}
.row .add{width:42px;height:22px;background:var(--brand);color:#fff;border-radius:2px;font-size:12px;display:flex;align-items:center;justify-content:center;margin-right:6px}
.note{left:898px;top:273px;width:214px;height:169px;background:var(--soft);border-radius:4px;padding:20px}
.note h3{font-size:16px;font-weight:500;margin-bottom:12px}
.note p{font-size:12.5px;line-height:20.5px;color:var(--muted)}
.pg{position:absolute;top:646px;height:31px;border-radius:2px;display:flex;align-items:center;justify-content:center;font-size:12px}
.footer-line{left:0;top:709px;width:1200px;height:1px;background:var(--line)}
.btn{position:absolute;top:723px;height:31px;border-radius:2px;display:flex;align-items:center;justify-content:center;font-size:12px;font-weight:500}
</style>
</head>
<body>
<header class="topbar">
  <div class="abs brand"><span class="brand-dot"></span>Skillora</div>
  <nav class="nav">
    <a class="active" style="left:488px">Assessments</a>
    <a style="left:588px">Colleagues</a>
    <a style="left:671px">Results</a>
  </nav>
  <svg class="abs" style="left:1029px;top:13px" width="18" height="18" viewBox="0 0 24 24" fill="none" stroke="#fff" stroke-width="1.6"><path d="M6 16V11a6 6 0 0 1 12 0v5l2 2H4z"/><path d="M10 21h4"/></svg>
  <svg class="abs" style="left:1064px;top:13px" width="18" height="18" viewBox="0 0 24 24" fill="none" stroke="#fff" stroke-width="1.6"><circle cx="12" cy="12" r="3"/><path d="M12 2l2 3 3.5-.7.7 3.5 3 2-2 3 1 3.4-3.4 1-.8 3.5-3.5-.7L12 22l-2-3-3.5.7-.7-3.5-3-2 2-3L3.8 7.8l3.4-1 .8-3.5 3.5.7z"/></svg>
  <div class="abs avatar-top" role="img" aria-label="User profile photo"></div>
</header>

<div class="abs crumbs">
  <svg width="20" height="20" viewBox="0 0 20 20" fill="none" stroke="#0e78bb" stroke-width="1.6"><circle cx="10" cy="10" r="9"/><path d="M14 10H6m3-3.5L5.5 10 9 13.5"/></svg>
  <span class="link">Assessment</span><span>/</span><span>Application Design Capabilities</span>
</div>
<div class="abs title">
  <svg width="22" height="22" viewBox="0 0 24 24" fill="none" stroke="#444" stroke-width="1.4"><path d="M16 10V3H4v18h8"/><path d="M7 7h6M7 11h5M7 15h3"/><circle cx="17" cy="17" r="4"/><path d="M15.3 17l1.2 1.2 2.2-2.2"/></svg>
  UI/UX Designer Assessment
</div>
<div class="abs score">80<small>%</small></div>
<div class="abs progress"><i></i></div>

<div class="abs infoband">
  <span class="item" style="left:88px">Assessment Date: <span class="v">Feb 12, 2024</span></span>
  <span class="sep" style="left:263px"></span>
  <span class="item" style="left:285px">Assessment Type: <span class="v">UI/UX Skill</span></span>
  <span class="sep" style="left:448px"></span>
  <span class="item" style="left:470px">Due Date: <span style="color:var(--muted)">17/02/2024</span></span>
  <span class="item" style="right:88px;color:var(--muted)">Last Updated: <span style="color:var(--ink)">23/05/2024</span></span>
</div>

<div class="steps">
  <div class="abs" style="left:88px;top:269px;width:1px;height:39px;background:var(--line)"></div>
  <svg class="dot" style="top:256px" viewBox="0 0 13 13"><circle cx="6.5" cy="6.5" r="6.5" fill="#13939b"/><path d="M3.8 6.6l1.8 1.8 3.6-3.6" stroke="#fff" stroke-width="1.4" fill="none"/></svg>
  <span class="label" style="top:254px;color:var(--brand)">Quiz</span>
  <span class="dot" style="top:302px;border:1px solid #c4c9cf;background:#fff"></span>
  <span class="label" style="top:300px">Endorsement</span>
</div>

<div class="abs section-h">Endorsement</div>
<div class="abs save">
  <svg width="15" height="15" viewBox="0 0 24 24" fill="none" stroke="#0e78bb" stroke-width="1.8"><path d="M4 3h13l3 3v15H4z"/><path d="M8 3v5h8V3M8 21v-7h8v7"/></svg>
  Save Progress
</div>
<div class="abs rule"></div>

<div class="field" style="left:366px;width:199px">All categories
  <svg width="10" height="10" viewBox="0 0 10 10" fill="none" stroke="#333" stroke-width="1.4"><path d="M2 3.5l3 3 3-3"/></svg></div>
<div class="field" style="left:572px;width:160px;color:#888">Search
  <svg width="15" height="15" viewBox="0 0 24 24" fill="none" stroke="#888" stroke-width="1.8"><circle cx="11" cy="11" r="7"/><path d="M16 16l5 5"/></svg></div>
<div class="field" style="left:735px;width:99px;color:#a7adb3;justify-content:center">Send Request</div>

<div class="row" style="top:318px"><span class="cb"></span><span class="pic" role="img" aria-label="Colleague photo" style="background:#8a5a3a"></span><span class="name">Mei Lin Chao</span><span class="role">Application Design Capabilities</span><span class="add">Add</span></div>
<div class="row" style="top:362px"><span class="cb"></span><span class="pic" role="img" aria-label="Colleague photo" style="background:#3d3a38"></span><span class="name">Harold Denton</span><span class="role">UI/UX Designer</span><span class="add">Add</span></div>
<div class="row" style="top:407px"><span class="cb"></span><span class="pic" role="img" aria-label="Colleague photo" style="background:#6b6b6e"></span><span class="name">Mark Tillman</span><span class="role">Front-end Developer</span><span class="add">Add</span></div>
<div class="row" style="top:451px"><span class="cb"></span><span class="pic" role="img" aria-label="Colleague photo" style="background:#e3b98c"></span><span class="name">Alina Kerr</span><span class="role">Cybersecurity Analyst</span><span class="add">Add</span></div>
<div class="row" style="top:496px"><span class="cb"></span><span class="pic" role="img" aria-label="Colleague photo" style="background:#9a7a66"></span><span class="name">Ronald Clay</span><span class="role">DevOps Engineer</span><span class="add">Add</span></div>
<div class="row" style="top:540px"><span class="cb"></span><span class="pic" role="img" aria-label="Colleague photo" style="background:#7a6548"></span><span class="name">Renee Dalton</span><span class="role">DevOps Engineer</span><span class="add">Add</span></div>
<div class="row" style="top:585px"><span class="cb"></span><span class="pic" role="img" aria-label="Colleague photo" style="background:#7fa9c4"></span><span class="name">Jake Morrow</span><span class="role">DevOps Engineer</span><span class="add">Add</span></div>

<aside class="abs note">
  <h3>Note</h3>
  <p>Lorem ipsum dolor sit amet, consecteteur adispiscing elit. Lorem ipsum dolor sit amet, consecteteur adispiscing elit.Lorem ipsum dolor.</p>
</aside>

<div class="pg" style="left:480px;width:82px;border:1px solid var(--line);color:#bbc0c5;font-size:11px">‹ Previous</div>
<div class="pg" style="left:576px;width:33px;background:var(--brand);color:#fff;font-size:13px">1</div>
<div class="pg" style="left:610px;width:33px;color:var(--muted);font-size:13px">2</div>
<div class="pg" style="left:656px;width:64px;background:var(--brand);color:#fff;font-weight:500">Next&nbsp;›</div>

<div class="abs footer-line"></div>
<div class="btn" style="left:88px;width:72px;border:1px solid var(--brand);color:var(--brand)">Go Back</div>
<div class="btn" style="left:990px;width:50px;color:var(--muted)">Skip&nbsp;›</div>
<div class="btn" style="left:1060px;width:52px;background:var(--brand);color:#fff">Next</div>
</body>
</html>
```